Stationary Set Rebrand for Brennick

We are a Canadian Distribution and Service Company that was established in 1969. Over the past 5 decades we have expanded our business and have warehouses across Canada. We specialize in adhesive tapes, adhesives, films, safety, warehouse, shipping, janitorial and packaging supplies.

We have updated our logo design and would like a new corporate branding identity that includes a new fresh Stationary Set (Business Cards, Letterhead, Letterhead MS Word, Envelope, Presentation Folders, Email Signatures, Notepad Covers, etc.)

Target Market(s)

Industrial Business Sector

Font styles to use
Sans Serif

Colors
0054AA
0677BA
7BADD7
CADEEF
E8F1F8
0094D4
00A9DD
6FCCEA
C7EBF8
E9F6FB
00AB8E
00BBA5
67D7C9
C6EFE9
E9F9F6
EB3D1F
EC4F4E
F09395
F8D3D4
FCEDEE

Requirements
Should not have
• Colors not too light, darker colours preferred

```html
<!DOCTYPE html>
<html lang="en">
<head>
<meta charset="utf-8">
<title>Brennick Stationery Set</title>
<link rel="stylesheet" href="https://fonts.googleapis.com/css2?family=Poppins:wght@400;500;600;700&family=Open+Sans:wght@400;600;700&display=swap">
<style>
:root{
  --brand-red:#da1f26;
  --ink:#111111;
  --paper:#ffffff;
  --backdrop:#d6dbdd;
  --night:#1d1c2a;
  --night-soft:#34333f;
  --body-text:#2a2a2a;
}
*{box-sizing:border-box;margin:0;padding:0}
html,body{width:1200px;height:684px;overflow:hidden}
body{background:linear-gradient(180deg,#dde1e3,var(--backdrop));font-family:"Poppins",sans-serif;color:var(--ink);position:relative}
.piece{position:absolute;background:var(--paper);overflow:hidden;box-shadow:0 4px 10px rgba(0,0,0,.18)}
.swoosh{position:absolute;left:0;bottom:0;width:100%}
.wordmark{font-family:"Poppins",sans-serif;font-weight:700;color:var(--ink);letter-spacing:-.02em;line-height:1;white-space:nowrap}
.wordmark.light{color:var(--paper)}
.contact-list{list-style:none}
.contact-list li{display:flex;align-items:center;gap:4px;white-space:nowrap}
.icon{flex:none}
/* envelope */
.envelope-front{left:50px;top:53px;width:271px;height:120px}
.envelope-front .wordmark{position:absolute;right:10px;top:12px;font-size:21px}
.envelope-front .address{position:absolute;left:197px;top:68px;font-family:"Open Sans",sans-serif;font-size:5.2px;line-height:1.25}
.envelope-front .contact-list{position:absolute;left:197px;top:85px;font-family:"Open Sans",sans-serif;font-size:5.2px;line-height:1.2}
.envelope-back{left:51px;top:187px;width:270px;height:120px}
.envelope-flap{position:absolute;left:2px;top:0;width:266px;height:40px;border-radius:0 0 10px 10px;background:var(--paper);box-shadow:0 3px 6px rgba(0,0,0,.15)}
.envelope-flap .seal{position:absolute;left:128px;top:15px;width:10px;height:10px;border-radius:50%;background:var(--brand-red)}
/* business cards */
.card-back{left:51px;top:316px;width:264px;height:151px;background:var(--night);border-bottom:2px solid var(--brand-red)}
.card-back .pattern{position:absolute;inset:0;background:linear-gradient(120deg,var(--night) 40%,var(--night-soft))}
.card-back .wordmark{position:absolute;left:52px;top:56px;font-size:36px}
.card-front{left:51px;top:483px;width:264px;height:151px}
.card-front .wordmark{position:absolute;left:9px;top:58px;font-size:24px}
.divider{position:absolute;width:1px;background:var(--brand-red)}
.card-front .divider{left:132px;top:26px;height:100px}
.person-name{font-family:"Poppins",sans-serif;font-weight:500;white-space:nowrap;line-height:1}
.person-name .first{color:var(--brand-red);font-weight:600}
.person-role{font-weight:500;line-height:1.2}
.card-front .details{position:absolute;left:152px;top:33px;font-size:7.3px}
.card-front .person-name{font-size:14px}
.card-front .address{margin-top:7px;line-height:1.35}
.card-front .contact-list{margin-top:6px;line-height:1.35}
/* letterhead */
.letterhead{left:353px;top:55px;width:318px;height:449px;font-family:"Open Sans",sans-serif}
.letterhead .wordmark{position:absolute;left:18px;top:18px;font-size:26px}
.letterhead .header-contact{position:absolute;right:19px;top:18px;text-align:right;font-family:"Poppins",sans-serif;font-size:6.6px;line-height:1.3}
.letterhead .header-contact li{justify-content:flex-end}
.letter-body{position:absolute;left:18px;top:102px;width:284px;font-size:5.9px;line-height:1.42;color:var(--body-text)}
.letter-body .date{margin-bottom:6px}
.letter-body .recipient{font-weight:700;font-size:8px;color:var(--ink)}
.letter-body .recipient-role{margin-bottom:5px}
.letter-body .salutation{font-weight:700;font-size:8px;color:var(--ink);margin:12px 0 5px}
.letter-body p{text-align:justify;margin-bottom:8px}
.signature-mark{width:86px;height:22px;margin-top:10px;background:linear-gradient(90deg,rgba(0,0,0,.06),rgba(0,0,0,.02))}
.signer{font-family:"Poppins",sans-serif;font-weight:600;font-size:13px;color:var(--ink);line-height:1.1;margin-top:2px}
/* email signature */
.email-signature{left:353px;top:526px;width:318px;height:106px}
.email-signature .wordmark{position:absolute;left:24px;top:35px;font-size:24px}
.email-signature .divider{left:159px;top:12px;height:86px}
.email-signature .details{position:absolute;left:186px;top:13px;font-size:6.8px}
.email-signature .person-name{font-size:13.5px}
.email-signature .address{margin-top:6px;line-height:1.35}
.email-signature .contact-list{margin-top:5px;line-height:1.3}
.social-dots{position:absolute;left:11px;bottom:6px;display:flex;gap:4px;z-index:2}
.social-dots span{width:5px;height:5px;border-radius:50%;background:var(--paper)}
/* folder */
.folder-cover{left:696px;top:55px;width:140px;height:262px;background:linear-gradient(110deg,#f4f4f4,#dcdcdc)}
.folder-cover .wordmark{position:absolute;right:10px;top:222px;font-size:17px}
.folder-inside{left:860px;top:66px;width:310px;height:248px;background:linear-gradient(90deg,#fafafa 0,#eaeaea 49%,#d3d3d3 50%,#e2e2e2 100%)}
.folder-pocket{position:absolute;right:0;bottom:0;width:150px;height:80px;background:var(--brand-red);border-radius:60px 0 0 0}
/* notepad */
.notepad{left:730px;top:345px;width:440px;height:285px;background:var(--night)}
.notepad .pattern{position:absolute;inset:0 0 0 40px;background:linear-gradient(150deg,#1a1a1a 30%,#3a3a3a 70%,#9a9a9a)}
.notepad .feature{position:absolute;left:170px;top:50px;width:170px;height:130px;border-radius:50%;background:radial-gradient(circle at 40% 50%,var(--brand-red),#c5151c 60%,rgba(0,0,0,0) 72%)}
.notepad .edge-band{position:absolute;left:0;top:0;bottom:0;width:12px;background:var(--brand-red);border-right:3px solid var(--paper)}
.notepad .binding{position:absolute;left:-4px;top:0;bottom:0;width:8px;background:repeating-linear-gradient(180deg,#555 0 4px,transparent 4px 9px)}
.notepad .wordmark{position:absolute;left:36px;bottom:22px;font-size:30px}
</style>
</head>
<body>

<svg width="0" height="0" style="position:absolute" aria-hidden="true">
  <defs>
    <symbol id="wave" viewBox="0 0 300 40" preserveAspectRatio="none">
      <path d="M0 2 C70 22 190 32 300 28 L300 40 L0 40Z" fill="#da1f26"/>
      <path d="M95 27 C175 33 245 28 300 17 L300 22 C245 32 175 35 95 28Z" fill="#111"/>
    </symbol>
    <symbol id="i-phone" viewBox="0 0 10 10"><path d="M2 1l2 2-1 1c.6 1.3 1.7 2.4 3 3l1-1 2 2-1.5 1.5C4 9 1 6 .5 2.5Z" fill="none" stroke="#da1f26" stroke-width="1"/></symbol>
    <symbol id="i-globe" viewBox="0 0 10 10"><circle cx="5" cy="5" r="4.2" fill="none" stroke="#da1f26" stroke-width="1"/><path d="M1 5h8M5 1c-2 2.5-2 5.5 0 8M5 1c2 2.5 2 5.5 0 8" fill="none" stroke="#da1f26" stroke-width=".8"/></symbol>
    <symbol id="i-mail" viewBox="0 0 10 10"><rect x="1" y="2.2" width="8" height="5.6" fill="none" stroke="#da1f26" stroke-width="1"/><path d="M1 2.5l4 3 4-3" fill="none" stroke="#da1f26" stroke-width="1"/></symbol>
    <symbol id="i-pin" viewBox="0 0 10 10"><path d="M5 9.5C3 7 2 5.5 2 4a3 3 0 016 0c0 1.5-1 3-3 5.5Z" fill="none" stroke="#da1f26" stroke-width="1"/><circle cx="5" cy="4" r="1" fill="#da1f26"/></symbol>
  </defs>
</svg>

<!-- Envelope front -->
<section class="piece envelope-front">
  <div class="wordmark">Brennick</div>
  <div class="address">88 Harbourline Rd. Unit 4<br>Mississauga, ON L5T 2K9</div>
  <ul class="contact-list">
    <li><svg class="icon" width="5" height="5"><use href="#i-phone"/></svg>(416) 555-0148</li>
    <li><svg class="icon" width="5" height="5"><use href="#i-mail"/></svg>hello@brennick.ca</li>
    <li><svg class="icon" width="5" height="5"><use href="#i-globe"/></svg>www.brennick.ca</li>
  </ul>
  <svg class="swoosh" height="28"><use href="#wave"/></svg>
</section>

<!-- Envelope back -->
<section class="piece envelope-back">
  <div class="envelope-flap"><span class="seal"></span></div>
</section>

<!-- Business card back -->
<section class="piece card-back">
  <div class="pattern" role="img" aria-label="Repeating embossed leaf pattern in dark grey tones"></div>
  <div class="wordmark light">Brennick</div>
</section>

<!-- Business card front -->
<section class="piece card-front">
  <div class="wordmark">Brennick</div>
  <span class="divider"></span>
  <div class="details">
    <div class="person-name"><span class="first">Dana</span> Whitlock</div>
    <div class="person-role">Founder &amp; CEO</div>
    <div class="address">88 Harbourline Rd. Unit 4<br>Mississauga, ON L5T 2K9</div>
    <ul class="contact-list">
      <li><svg class="icon" width="6" height="6"><use href="#i-phone"/></svg>(416) 555-0148</li>
      <li><svg class="icon" width="6" height="6"><use href="#i-globe"/></svg>hello@brennicksupply.ca</li>
      <li><svg class="icon" width="6" height="6"><use href="#i-mail"/></svg>www.brennicksupply.ca</li>
    </ul>
  </div>
  <svg class="swoosh" height="34"><use href="#wave"/></svg>
</section>

<!-- Letterhead -->
<section class="piece letterhead">
  <div class="wordmark">Brennick</div>
  <ul class="contact-list header-contact">
    <li>(416) 555-0148<svg class="icon" width="6" height="6"><use href="#i-phone"/></svg></li>
    <li>hello@brennicksupply.ca<svg class="icon" width="6" height="6"><use href="#i-globe"/></svg></li>
    <li>www.brennicksupply.ca<svg class="icon" width="6" height="6"><use href="#i-mail"/></svg></li>
    <li>88 Harbourline Rd. Unit 4<svg class="icon" width="6" height="6"><use href="#i-pin"/></svg></li>
    <li style="padding-right:10px">Mississauga, ON L5T 2K9</li>
  </ul>
  <div class="letter-body">
    <div class="date">August-05-2019</div>
    <div class="recipient">Irene Castell</div>
    <div class="recipient-role">Director</div>
    <div>88 Harbourline Rd. Unit 4<br>Mississauga, ON L5T 2K9</div>
    <div class="salutation">Irene Castell</div>
    <p>Lorem ipsum dolor sit amet, consectetuer adipiscing elit, sed diam nonummy nibh euismod tincidunt ut laoreet dolore magna aliquam erat volutpat. Ut wisi enim ad minim veniam, quis nostrud exerci tation ullamcorper suscipit lobortis</p>
    <p>Lorem ipsum dolor sit amet, cons ectetuer adipiscing elit, sed diam nonummy nibh euismod tincidunt ut laoreet dolore magna aliquam erat volutpat. Ut wisi enim ad minim veniam, quis nostrud exerci tation ullamcorper suscipit lobortis nisl ut aliquip ex ea commodo consequat. Lorem ipsum dolor sit amet, consectetuer olutpat. Ut wisi enim ad minim veniam, quis nostrud exerci tation ullamcorper suscipit lobortis nisl ut aliquip ex ea commodo consequat. Duis autem</p>
    <p>vel eum iriure dolor in hendrerit in vulputate velit esse molestie consequat, vel illum dolore eu feugiat nulla facilisis at vero eros et accumsan et iusto odio dignissim qui blandit praesent luptatum zzril delenit augue duis dolore te feugait nulla facilisi. Lorem ipsum dolor sit amet, cons ectetuer adipiscing elit, sed diam nonummy nibh euismod tincidunt ut laoreet dolore magna aliquam erat volutpat. Ut wisi enim .</p>
    <div class="signature-mark" role="img" aria-label="Handwritten signature"></div>
    <div class="signer">Owen Pryce</div>
    <div>Co-Founder</div>
  </div>
  <svg class="swoosh" height="32"><use href="#wave"/></svg>
</section>

<!-- Email signature -->
<section class="piece email-signature">
  <div class="wordmark">Brennick</div>
  <span class="divider"></span>
  <div class="details">
    <div class="person-name"><span class="first">Dana</span> Whitlock</div>
    <div class="person-role">Founder &amp; CEO</div>
    <div class="address">88 Harbourline Rd. Unit 4<br>Mississauga, ON L5T 2K9</div>
    <ul class="contact-list">
      <li><svg class="icon" width="6" height="6"><use href="#i-phone"/></svg>(416) 555-0148</li>
      <li><svg class="icon" width="6" height="6"><use href="#i-globe"/></svg>hello@brennicksupply.ca</li>
      <li><svg class="icon" width="6" height="6"><use href="#i-mail"/></svg>www.brennicksupply.ca</li>
    </ul>
  </div>
  <div class="social-dots"><span></span><span></span><span></span><span></span><span></span></div>
  <svg class="swoosh" height="30"><use href="#wave"/></svg>
</section>

<!-- Presentation folder cover -->
<section class="piece folder-cover">
  <div class="wordmark">Brennick</div>
  <svg class="swoosh" height="34"><use href="#wave"/></svg>
</section>

<!-- Presentation folder inside -->
<section class="piece folder-inside">
  <div class="folder-pocket"></div>
</section>

<!-- Notepad cover -->
<section class="piece notepad">
  <div class="pattern" role="img" aria-label="Embossed leaf pattern fading from black to silver"></div>
  <div class="feature" role="img" aria-label="Large red leaf graphic"></div>
  <div class="edge-band"></div>
  <div class="binding"></div>
  <div class="wordmark light">Brennick</div>
</section>

</body>
</html>
```